Veranix - Solution provider in business consulting

Veranix is a swiss based company providing solutions for developing markets. The business covers various fields of business consulting, such as supply chain, product costs, quality management and manufacturing management. The Business operates in a efficient, straight and solution oriented manner.
The final design should communicate these characteristics. Asian people as well as as western people shall identify the qualities of the company at first sight.
The customer needs business cards with a simple view but an recognizable design, printed in high quality. Engraved elements such as the globe or simple words are possible.
Available colors are: (RAL)
102/102/102
51/102/102
153/204/153
255/102/51
Font: Calibri

```html
<!DOCTYPE html>
<html lang="en">
<head>
<meta charset="utf-8">
<title>Veranix business cards</title>
<link rel="stylesheet" href="https://fonts.googleapis.com/css2?family=Carlito:wght@400;700&display=swap">
<style>
  :root {
    --stage: #e9e7e4;
    --card-white: #ffffff;
    --band-grey: #666666;
    --ink-grey: #666666;
    --text-light: #ffffff;
  }
  * { box-sizing: border-box; margin: 0; padding: 0; }
  html, body { width: 1200px; height: 900px; overflow: hidden; }
  body {
    position: relative;
    background: var(--stage);
    font-family: "Carlito", Calibri, sans-serif;
  }
  .card {
    position: absolute;
    background: var(--card-white);
    overflow: hidden;
    box-shadow: 0 4px 14px rgba(0,0,0,0.12);
  }
  /* Front card */
  .card-front { left: 77px; top: 34px; width: 589px; height: 364px; }
  .front-brand {
    position: absolute; left: 0; top: 0; width: 100%; height: 156px;
    display: flex; align-items: center; padding-left: 30px; gap: 14px;
  }
  .brand-dot {
    width: 58px; height: 58px; border-radius: 50%;
    background: var(--ink-grey);
  }
  .brand-name {
    font-size: 52px; font-weight: 400; color: var(--ink-grey);
    letter-spacing: 1px;
  }
  .front-band {
    position: absolute; left: 0; top: 156px; width: 100%; height: 208px;
    background: var(--band-grey); color: var(--text-light);
    padding: 4px 30px 0 31px;
  }
  .person-name { font-size: 22px; font-weight: 700; line-height: 26px; }
  .person-role { font-size: 16px; line-height: 20px; margin-bottom: 12px; }
  .contact-list { list-style: none; }
  .contact-item {
    display: flex; align-items: center; gap: 10px;
    font-size: 16px; line-height: 24.5px;
  }
  .contact-icon { width: 12px; height: 12px; flex: none; }
  .company-address { font-size: 16px; margin-top: 10px; }
  /* Back card */
  .card-back { left: 388px; top: 505px; width: 566px; height: 352px; }
  .back-band {
    position: absolute; left: 0; top: 110px; width: 100%; height: 130px;
    background: var(--band-grey);
    display: flex; align-items: center; justify-content: center;
  }
  .back-name {
    font-size: 80px; font-weight: 400; color: var(--text-light);
    letter-spacing: 1px; padding-top: 6px;
  }
</style>
</head>
<body>
  <section class="card card-front">
    <div class="front-brand">
      <span class="brand-dot"></span>
      <span class="brand-name">veranix</span>
    </div>
    <div class="front-band">
      <p class="person-name">Marco Keller</p>
      <p class="person-role">CEO</p>
      <ul class="contact-list">
        <li class="contact-item">
          <svg class="contact-icon" viewBox="0 0 12 12" aria-hidden="true"><rect x="2.5" y="0.5" width="7" height="11" rx="1" fill="none" stroke="#fff" stroke-width="1.3"/><rect x="5" y="9" width="2" height="1.2" fill="#fff"/></svg>
          +41 79 555 0182
        </li>
        <li class="contact-item">
          <svg class="contact-icon" viewBox="0 0 12 12" aria-hidden="true"><path d="M2.5 0.8 L4.6 3.2 L3.4 4.6 C4.2 6.3 5.7 7.8 7.4 8.6 L8.8 7.4 L11.2 9.5 L9.8 11.2 C5.3 10.6 1.4 6.7 0.8 2.2 Z" fill="#fff"/></svg>
          +41 71 555 0347
        </li>
        <li class="contact-item">
          <svg class="contact-icon" viewBox="0 0 12 12" aria-hidden="true"><rect x="0.5" y="2.5" width="11" height="7.5" fill="#fff"/><path d="M0.8 2.8 L6 7 L11.2 2.8" fill="none" stroke="#666" stroke-width="1"/></svg>
          marco.keller@veranix.ch
        </li>
        <li class="contact-item">
          <svg class="contact-icon" viewBox="0 0 12 12" aria-hidden="true"><circle cx="6" cy="6" r="5.5" fill="#fff"/><path d="M6 0.5 V11.5 M0.5 6 H11.5" stroke="#666" stroke-width="0.8"/></svg>
          www.veranix.ch
        </li>
      </ul>
      <p class="company-address">Veranix GmbH Feldweg 14 9000 Talberg Switzerland</p>
    </div>
  </section>

  <section class="card card-back">
    <div class="back-band">
      <span class="back-name">veranix</span>
    </div>
  </section>
</body>
</html>
```